Innovative cost reduction consultant needs to build a group of technical advisors

We need to share our message and compassion for developing cost reduction in the automotive industry. We create opportunities for immediate innovation, by developing cost reduction solutions across suppliers with related process. Attached is an existing Power Point, but it needs improvement. Most of all, a good compelling story, why experts should join us.

Target Market(s)

Automotive industry, supply chain management

Industry/Entity Type

Automotive

Font styles to use
Serif
Sans Serif

Requirements
Must have
• Better visual graphics. There are a few, but they are not as visually appearing as I would like. A graphic with data should have a better visual impact then the ones that I created. I would like to share the message, that I am providing a solution for the automotive industry. The goal is to reduce costs and improve supplier and OEM relationships. The objective is to do so by creating opportunities for immediate innovation, by developing cost reduction solutions across suppliers with related processes. This message may need a visual graphic, which is missing from the presentation.
Nice to have
• Challenge my story and presentation. Does this make sense to you, and what is your opinions of the subject. Or, a relevant news source to validate the story.
Should not have
• I have not decided on the name of the venture or logo. So, let's just use my name as the source or writer. Marcus Delby, Cost Reduction Specialist. Thanks,

```html
<!DOCTYPE html>
<html lang="en">
<head>
<meta charset="utf-8">
<title>Survey Data</title>
<link rel="stylesheet" href="https://fonts.googleapis.com/css2?family=Roboto+Condensed:wght@400;700&family=Arimo:wght@400;700&display=swap">
<style>
  :root{
    --brand-blue:#0f5fae;
    --brand-blue-deep:#0a4f98;
    --band-blue:#1b8be0;
    --diagram-blue:#1a8fe3;
    --diagram-dark:#3d3d3d;
    --frame-gray:#b9b9b9;
    --text-gray:#5a5a5a;
    --ink:#222;
    --cell-red:#e8483b;
    --cell-orange:#f39a55;
    --cell-yellow:#f5de5f;
    --cell-green:#5fb04a;
    --total-blue:#a9c0e6;
    --potential-bar:#8fc3ef;
    --grid:#d6d6d6;
  }
  *{box-sizing:border-box;margin:0;padding:0}
  html,body{width:1200px;height:650px;overflow:hidden;background:#fff}
  .slide{position:relative;width:1200px;height:650px;overflow:hidden;background:#fff;font-family:"Arimo",Arial,sans-serif}
  .header-band{position:absolute;left:0;top:0;width:1200px;height:106px;background:linear-gradient(180deg,var(--brand-blue-deep) 0%,var(--brand-blue) 100%)}
  .footer-band{position:absolute;left:0;top:622px;width:1200px;height:28px;background:var(--band-blue)}
  .slide-title{position:absolute;left:94px;top:44px;font-family:"Roboto Condensed",Arial,sans-serif;font-weight:700;font-size:45px;line-height:1;color:#fff;letter-spacing:-.3px}
  .points{position:absolute;left:88px;top:114px;list-style:none}
  .points li{position:relative;padding-left:24px;font-family:"Roboto Condensed",Arial,sans-serif;font-size:20px;color:var(--text-gray);line-height:34px}
  .points li::before{content:"";position:absolute;left:2px;top:10px;border-left:9px solid var(--diagram-blue);border-top:6px solid transparent;border-bottom:6px solid transparent}

  .base-condition{position:absolute;left:108px;top:194px;width:98px;height:395px;background:var(--diagram-blue);display:flex;align-items:center;justify-content:center}
  .base-condition span{transform:rotate(-90deg);white-space:nowrap;font-family:"Roboto Condensed",Arial,sans-serif;font-weight:700;font-size:37px;color:#fff}
  .target-frame{position:absolute;left:219px;top:194px;width:152px;height:288px;border:3px solid var(--frame-gray)}
  .target-arrow{position:absolute;left:0;top:0}
  .target-label{position:absolute;left:8px;right:8px;top:136px;height:100px;background:#fff;display:flex;align-items:center;justify-content:center;text-align:center;font-family:"Roboto Condensed",Arial,sans-serif;font-weight:700;font-size:24px;line-height:1.1;color:var(--diagram-dark)}
  .individual-effort{position:absolute;left:219px;top:496px;width:152px;height:93px;background:var(--diagram-dark);display:flex;align-items:center;justify-content:center;text-align:center;font-family:"Roboto Condensed",Arial,sans-serif;font-weight:700;font-size:22px;line-height:1.08;color:#fff}

  .survey-panel{position:absolute;left:410px;top:48px;width:768px;height:548px;background:#fff;border:1px solid #cfcfcf;box-shadow:0 2px 6px rgba(0,0,0,.25);padding:6px}
  .survey-table{width:100%;border-collapse:collapse;table-layout:fixed;font-size:6.6px;color:var(--ink)}
  .survey-table th,.survey-table td{height:10.5px;padding:0 2px;line-height:1;white-space:nowrap;overflow:hidden;border-bottom:1px solid var(--grid);border-right:1px solid var(--grid);text-align:right}
  .survey-table th{font-weight:700;text-align:center;height:14px}
  .survey-table td:first-child,.survey-table th:first-child{text-align:left}
  .survey-table .r{background:var(--cell-red)}
  .survey-table .o{background:var(--cell-orange)}
  .survey-table .y{background:var(--cell-yellow)}
  .survey-table .g{background:var(--cell-green)}
  .survey-table .potential{font-weight:700;background:linear-gradient(90deg,var(--potential-bar) var(--w,0%),transparent var(--w,0%))}
  .survey-table .totals td{background:var(--total-blue);font-weight:700;height:12px}
</style>
</head>
<body>
<div class="slide">
  <div class="header-band"></div>
  <h1 class="slide-title">Survey Data</h1>
  <ul class="points">
    <li>Gap analysis</li>
    <li>Missed opportunities</li>
  </ul>

  <div class="base-condition"><span>Supplier Base Condition</span></div>
  <div class="target-frame">
    <svg class="target-arrow" width="146" height="282" viewBox="0 0 146 282">
      <line x1="73" y1="10" x2="73" y2="272" stroke="#1a8fe3" stroke-width="2"/>
      <polygon points="73,2 67,13 79,13" fill="#1a8fe3"/>
      <polygon points="73,280 67,269 79,269" fill="#1a8fe3"/>
    </svg>
    <div class="target-label">-A% Cost<br>Reduction<br>Target</div>
  </div>
  <div class="individual-effort">Supplier<br>individual<br>effort</div>

  <div class="survey-panel">
    <table class="survey-table">
      <colgroup>
        <col style="width:8%"><col style="width:9.5%"><col style="width:11%"><col style="width:9%"><col style="width:9%"><col style="width:8%"><col style="width:9%"><col style="width:9%"><col style="width:8%"><col style="width:7%"><col style="width:12.5%">
      </colgroup>
      <thead>
        <tr><th>Account</th><th>Annual Revenue</th><th>3% Cost improvement</th><th>Raw Material</th><th>Machine process</th><th>Assembly</th><th>Components</th><th>Packaging</th><th>Tooling</th><th>QC</th><th>Ttl. Potential %</th></tr>
      </thead>
      <tbody>
        <tr><td>Supplier X</td><td>$42,000,000.00</td><td>$1,260,000.00</td><td class="y">$18,687.00</td><td class="y">$10,000.00</td><td></td><td></td><td></td><td class="y">$20,000.00</td><td></td><td class="potential" style="--w:17.6%">$48,687.00</td></tr>
        <tr><td>Supplier X</td><td>$19,138,671.00</td><td>$574,160.13</td><td></td><td></td><td></td><td></td><td></td><td class="g">$30,000.00</td><td></td><td class="potential" style="--w:10.9%">$30,000.00</td></tr>
        <tr><td>Supplier X</td><td>$29,800,000.00</td><td>$894,000.00</td><td></td><td class="y">$13,410.00</td><td></td><td></td><td></td><td></td><td></td><td class="potential" style="--w:4.9%">$13,410.00</td></tr>
        <tr><td>Supplier X</td><td>$20,000,000.00</td><td></td><td></td><td></td><td></td><td></td><td></td><td></td><td></td><td></td></tr>
        <tr><td></td><td></td><td>$600,000.00</td><td></td><td></td><td class="o">$3,000.00</td><td class="o">$3,000.00</td><td class="y">$3,000.00</td><td></td><td></td><td class="potential" style="--w:3.3%">$9,000.00</td></tr>
        <tr><td>Supplier X</td><td>$24,937,124.00</td><td>$748,113.72</td><td class="r">$3,740.00</td><td class="r">$3,740.00</td><td></td><td></td><td class="y">$3,740.00</td><td></td><td></td><td class="potential" style="--w:4.1%">$11,220.00</td></tr>
        <tr><td>Supplier X</td><td>$637,300,000.00</td><td>$19,119,000.00</td><td class="g">$71,500.00</td><td class="g">$56,000.00</td><td></td><td class="g">$66,000.00</td><td class="g">$82,000.00</td><td></td><td></td><td class="potential" style="--w:100%">$276,500.00</td></tr>
        <tr><td>Supplier X</td><td>$24,937,124.00</td><td>$748,113.72</td><td></td><td></td><td class="y">$5,000.00</td><td class="y">$6,000.00</td><td></td><td></td><td></td><td class="potential" style="--w:4%">$11,000.00</td></tr>
        <tr><td>Supplier X</td><td>$114,454,560.00</td><td>$3,433,636.80</td><td class="y">$25,000.00</td><td class="y">$14,000.00</td><td class="y">$4,000.00</td><td class="y">$8,000.00</td><td class="r">$500.00</td><td></td><td></td><td class="potential" style="--w:18.6%">$51,504.00</td></tr>
        <tr><td>Supplier X</td><td>$12,100,000.00</td><td>$363,000.00</td><td></td><td class="o">$400.00</td><td class="o">$2,200.00</td><td></td><td></td><td></td><td class="g">$3,200.00</td><td class="potential" style="--w:2.1%">$5,800.00</td></tr>
        <tr><td>Supplier X</td><td>$20,000,000.00</td><td>$600,000.00</td><td></td><td class="y">$3,000.00</td><td></td><td class="o">$3,000.00</td><td></td><td class="y">$3,000.00</td><td></td><td class="potential" style="--w:3.3%">$9,000.00</td></tr>
        <tr><td>Supplier X</td><td>$20,000,000.00</td><td>$600,000.00</td><td class="r">$3,000.00</td><td></td><td class="o">$3,000.00</td><td></td><td class="y">$3,000.00</td><td></td><td></td><td class="potential" style="--w:3.3%">$9,000.00</td></tr>
        <tr><td>Supplier X</td><td>$100,000,000.00</td><td>$3,000,000.00</td><td class="o">$5,000.00</td><td class="y">$13,000.00</td><td class="y">$2,500.00</td><td class="y">$20,000.00</td><td class="y">$4,000.00</td><td></td><td></td><td class="potential" style="--w:16.1%">$44,500.00</td></tr>
        <tr><td>Supplier X</td><td>$2,500,000.00</td><td>$75,000.00</td><td></td><td></td><td class="o">$1,125.00</td><td></td><td></td><td></td><td></td><td class="potential" style="--w:0.4%">$1,125.00</td></tr>
        <tr><td>Supplier X</td><td>$100,000,000.00</td><td>$3,000,000.00</td><td></td><td class="y">$20,000.00</td><td class="y">$25,000.00</td><td></td><td></td><td></td><td></td><td class="potential" style="--w:16.3%">$45,000.00</td></tr>
        <tr><td>Supplier X</td><td>$29,000,000.00</td><td>$870,000.00</td><td class="r">$3,000.00</td><td class="y">$5,000.00</td><td></td><td class="y">$5,000.00</td><td></td><td></td><td></td><td class="potential" style="--w:4.7%">$13,000.00</td></tr>
        <tr><td>Supplier X</td><td>$29,000,000.00</td><td>$870,000.00</td><td></td><td></td><td class="y">$5,000.00</td><td></td><td class="y">$3,000.00</td><td class="y">$5,000.00</td><td></td><td class="potential" style="--w:4.7%">$13,000.00</td></tr>
        <tr><td>Supplier X</td><td>$20,000,000.00</td><td>$600,000.00</td><td></td><td></td><td class="y">$5,000.00</td><td class="y">$4,000.00</td><td></td><td></td><td></td><td class="potential" style="--w:3.3%">$9,000.00</td></tr>
        <tr><td>Supplier X</td><td>$47,200,000.00</td><td>$1,416,000.00</td><td class="y">$8,000.00</td><td class="y">$10,000.00</td><td></td><td class="o">$240.00</td><td class="y">$3,000.00</td><td></td><td></td><td class="potential" style="--w:7.7%">$21,240.00</td></tr>
        <tr><td>Supplier X</td><td>$20,000,000.00</td><td>$600,000.00</td><td></td><td class="y">$3,000.00</td><td class="o">$3,000.00</td><td class="y">$3,000.00</td><td></td><td></td><td></td><td class="potential" style="--w:3.3%">$9,000.00</td></tr>
        <tr><td>Supplier X</td><td>$500,000.00</td><td>$15,000.00</td><td></td><td></td><td></td><td></td><td></td><td></td><td class="r">$225.00</td><td class="potential" style="--w:0.3%">$225.00</td></tr>
        <tr><td>Supplier X</td><td>$100,000,000.00</td><td>$3,000,000.00</td><td class="y">$10,000.00</td><td class="y">$10,000.00</td><td class="y">$10,000.00</td><td class="y">$12,000.00</td><td class="y">$2,500.00</td><td></td><td></td><td class="potential" style="--w:16.1%">$44,500.00</td></tr>
        <tr><td>Supplier X</td><td>$90,800,000.00</td><td>$2,724,000.00</td><td></td><td></td><td class="y">$10,000.00</td><td class="y">$10,000.00</td><td class="y">$10,000.00</td><td class="y">$10,000.00</td><td class="y">$660.00</td><td class="potential" style="--w:14.7%">$40,660.00</td></tr>
        <tr><td>Supplier X</td><td>$20,000,000.00</td><td>$600,000.00</td><td class="y">$9,000.00</td><td></td><td></td><td></td><td></td><td></td><td></td><td class="potential" style="--w:3.3%">$9,000.00</td></tr>
        <tr><td>Supplier X</td><td>$100,000,000.00</td><td>$3,000,000.00</td><td class="y">$15,000.00</td><td class="y">$15,000.00</td><td class="y">$15,000.00</td><td></td><td></td><td></td><td></td><td class="potential" style="--w:16.3%">$45,000.00</td></tr>
        <tr><td>Supplier X</td><td>$500,000.00</td><td>$15,000.00</td><td></td><td></td><td></td><td></td><td></td><td></td><td class="r">$225.00</td><td class="potential" style="--w:0.3%">$225.00</td></tr>
        <tr><td>Supplier X</td><td>$27,400,000.00</td><td>$822,000.00</td><td></td><td></td><td class="y">$6,000.00</td><td class="y">$8,000.00</td><td></td><td></td><td></td><td class="potential" style="--w:5.1%">$14,000.00</td></tr>
        <tr><td>Supplier X</td><td>$500,000.00</td><td>$15,000.00</td><td></td><td class="r">$225.00</td><td></td><td></td><td></td><td></td><td></td><td class="potential" style="--w:0.3%">$225.00</td></tr>
        <tr><td>Supplier X</td><td>$100,000,000.00</td><td>$3,000,000.00</td><td class="o">$5,000.00</td><td class="o">$12,000.00</td><td class="y">$5,000.00</td><td class="o">$20,000.00</td><td class="o">$2,500.00</td><td class="r">$500.00</td><td></td><td class="potential" style="--w:16.3%">$45,000.00</td></tr>
        <tr><td>Supplier X</td><td>$100,000,000.00</td><td>$3,000,000.00</td><td class="o">$5,000.00</td><td class="o">$12,000.00</td><td class="y">$5,000.00</td><td class="y">$20,000.00</td><td class="y">$2,500.00</td><td class="r">$500.00</td><td></td><td class="potential" style="--w:16.3%">$45,000.00</td></tr>
        <tr><td>Supplier X</td><td>$500,000,000.00</td><td>$15,000,000.00</td><td class="g">$120,000.00</td><td class="g">$55,000.00</td><td class="g">$43,000.00</td><td class="y">$7,000.00</td><td></td><td></td><td></td><td class="potential" style="--w:81.4%">$225,000.00</td></tr>
        <tr><td>Supplier X</td><td>$50,000,000.00</td><td>$1,500,000.00</td><td></td><td></td><td class="y">$10,000.00</td><td class="y">$10,000.00</td><td class="y">$2,500.00</td><td></td><td></td><td class="potential" style="--w:8.1%">$22,500.00</td></tr>
        <tr><td>Supplier X</td><td>$50,000,000.00</td><td>$1,500,000.00</td><td></td><td></td><td class="y">$10,000.00</td><td class="y">$10,000.00</td><td class="y">$2,500.00</td><td></td><td></td><td class="potential" style="--w:8.1%">$22,500.00</td></tr>
        <tr><td>Supplier X</td><td>$20,000,000.00</td><td>$600,000.00</td><td></td><td class="y">$9,000.00</td><td></td><td></td><td></td><td></td><td></td><td class="potential" style="--w:3.3%">$9,000.00</td></tr>
        <tr><td>Supplier X</td><td>$40,000,000.00</td><td>$1,200,000.00</td><td class="o">$5,000.00</td><td class="o">$5,000.00</td><td class="y">$5,000.00</td><td></td><td></td><td class="y">$3,000.00</td><td></td><td class="potential" style="--w:6.5%">$18,000.00</td></tr>
        <tr><td>Supplier X</td><td>$98,549,352.00</td><td>$2,956,480.56</td><td></td><td class="o">$22,000.00</td><td class="r">$500.00</td><td class="o">$347.00</td><td></td><td class="g">$20,000.00</td><td class="g">$2,500.00</td><td class="potential" style="--w:16.4%">$45,347.00</td></tr>
        <tr><td>Supplier X</td><td>$20,000,000.00</td><td>$600,000.00</td><td class="y">$8,000.00</td><td class="o">$1,000.00</td><td class="o">$2,000.00</td><td></td><td></td><td></td><td></td><td class="potential" style="--w:4%">$11,000.00</td></tr>
        <tr><td>Supplier X</td><td>$9,000,000.00</td><td>$270,000.00</td><td></td><td></td><td class="y">$4,050.00</td><td></td><td></td><td></td><td></td><td class="potential" style="--w:1.5%">$4,050.00</td></tr>
        <tr><td>Supplier X</td><td>$50,000,000.00</td><td>$1,500,000.00</td><td class="y">$8,000.00</td><td class="y">$5,000.00</td><td class="o">$4,000.00</td><td class="o">$3,000.00</td><td></td><td class="o">$2,500.00</td><td></td><td class="potential" style="--w:8.1%">$22,500.00</td></tr>
        <tr><td>Supplier X</td><td>$100,000,000.00</td><td>$3,000,000.00</td><td class="y">$10,000.00</td><td class="y">$10,000.00</td><td class="y">$10,000.00</td><td class="y">$5,000.00</td><td class="y">$5,000.00</td><td></td><td></td><td class="potential" style="--w:14.5%">$40,000.00</td></tr>
        <tr><td>Supplier X</td><td>$100,000,000.00</td><td>$3,000,000.00</td><td class="y">$10,000.00</td><td class="y">$10,000.00</td><td class="y">$10,000.00</td><td class="y">$5,000.00</td><td class="y">$5,000.00</td><td></td><td></td><td class="potential" style="--w:14.5%">$40,000.00</td></tr>
        <tr><td>Supplier X</td><td>$128,000,000.00</td><td>$3,840,000.00</td><td class="y">$20,000.00</td><td class="y">$22,000.00</td><td class="y">$5,000.00</td><td class="r">$1,600.00</td><td class="y">$4,000.00</td><td class="y">$5,000.00</td><td class="y">$600.00</td><td class="potential" style="--w:20.8%">$57,600.00</td></tr>
        <tr><td>Supplier X</td><td>$33,900,000.00</td><td>$1,017,000.00</td><td></td><td class="o">$5,000.00</td><td class="o">$8,000.00</td><td class="o">$2,255.00</td><td></td><td></td><td></td><td class="potential" style="--w:5.5%">$15,255.00</td></tr>
        <tr><td>Supplier X</td><td>$10,000,000.00</td><td>$300,000.00</td><td class="o">$4,500.00</td><td></td><td></td><td></td><td></td><td></td><td></td><td class="potential" style="--w:1.6%">$4,500.00</td></tr>
        <tr><td>Supplier X</td><td>$20,000,000.00</td><td>$600,000.00</td><td class="r">$3,000.00</td><td class="o">$3,000.00</td><td class="y">$3,000.00</td><td></td><td></td><td class="y">$500.00</td><td></td><td class="potential" style="--w:3.4%">$9,500.00</td></tr>
        <tr><td>Supplier X</td><td>$13,600,000.00</td><td>$408,000.00</td><td class="y">$6,120.00</td><td></td><td></td><td></td><td></td><td></td><td></td><td class="potential" style="--w:2.2%">$6,120.00</td></tr>
        <tr><td>Supplier X</td><td>$100,000,000.00</td><td>$3,000,000.00</td><td class="y">$15,000.00</td><td class="y">$15,000.00</td><td class="y">$15,000.00</td><td></td><td></td><td></td><td></td><td class="potential" style="--w:16.3%">$45,000.00</td></tr>
        <tr><td></td><td></td><td></td><td></td><td></td><td></td><td></td><td></td><td></td><td></td><td class="potential">$0.00</td></tr>
        <tr class="totals"><td></td><td>$3,285,216,831.00</td><td>$95,853,504.93</td><td>$385,367.00</td><td>$361,775.00</td><td>$245,495.00</td><td>$233,842.00</td><td>$138,744.00</td><td>$99,500.00</td><td>$8,110.00</td><td>$1,751,210.00</td></tr>
      </tbody>
    </table>
  </div>

  <div class="footer-band"></div>
</div>
</body>
</html>
```